Sunset Harbor Living Web Page

We need a web page design that has two intro pages - first being a 'home page', then a link to the second page that has the 'content tabs' and a 'call to action' (see below).

The business helps people that wish to retire to S.E.Asia (Thailand, Malaysia, Indonesia,The Philippines etc) - to enjoy the lifestyle and the remaining years of their lives. What attracts S.E.Asia to many people is the lower cost, the atmoshpere and beauty of the tropics and the vibrancy of the various countries.

People that are wishing to make the most of their retirement and are adventurous at a great bargain compared to the cost of their own countries will be interested.

We help them achieve this - visa, financials (tax, gov't payments etc), introduce them to the right people for property, clubs, retirement facilities, insurance and so forth.

Therefore we are providing an extremely wide ranging service and this site will provide broad but general information only - with a call to action to come and see us for more specific information and how we can help them specifically.

This site will be predominantly for travel and lifestyle, it will be linked with another financial services (financial planning) site later down the track.

The colour scheme is dark green and blue - as per the attached logo design. Photos and background just think lifestyle and S.E.Asia - beaches/mountains/water/recreational activities for retirees.

Target market is mostly those coming up to retirement to those that are already retired. But we also expect to have some interest with younger people that would like to find out more and plan for the future. So a broad age group but I would say mostly 40-70 yrs old.

On the first (Home) page we would like our company name 'Sunset Harbor Living', our logo (which will be on all pages) and a statement such as: “Imagine a retirement where your dreams are brought to life, and you have never felt more alive. Let us show you how”. Then a link to the second page.

We would like an uncluttered site. On the second (contents) page the tabs would be:

- Visa
- Property
- Financials
- Travel
- Insurance & Healthcare
- Medical Tourism
- Cost of living
- Weekly Blogs and articles
- Sunset Harbor Living story

We would also like a call to action on the second page - asking them to leave their contact details if they wish to learn more or sign up to our weekly newsletter/blog.

We are open to suggestions and your imaginations.

Thank you
Malcolm

Font styles to use
Serif
Script

Colors
0255a3
3377b5
00a990
9bcb3c
abd036
33b8a4
85abd2
cadf82
86cfc6

Requirements
Must have
• I have been asked by the web designer to receive a 'Web Font' so that we can 'get off of Zentrofy'. Hope that makes sense.

```html
<!DOCTYPE html>
<html lang="en">
<head>
<meta charset="utf-8">
<title>Sunset Harbor Living — Home</title>
<link rel="stylesheet" href="https://fonts.googleapis.com/css2?family=Oswald:wght@500;600&family=Poppins:wght@600&display=swap">
<style>
  :root {
    --brand-blue: #0255a3;
    --mid-blue: #3377b5;
    --brand-green: #00a990;
    --ink: #0b0b0b;
    --white: #ffffff;
    --panel: rgba(255, 255, 255, 0.55);
  }
  * { box-sizing: border-box; margin: 0; padding: 0; }
  html, body { width: 1200px; height: 810px; overflow: hidden; background: var(--white); }
  .home {
    position: relative;
    width: 1200px;
    height: 810px;
    overflow: hidden;
    font-family: "Oswald", sans-serif;
  }
  .home__scene {
    position: absolute;
    inset: 0;
    background:
      linear-gradient(115deg, rgba(120, 200, 200, 0.55) 0%, rgba(120, 200, 200, 0) 45%),
      linear-gradient(180deg, #3f93dc 0%, #8cc2ec 22%, #d9ecf8 40%, #dfeee6 52%, #b9d6b0 58%, #d8e4d2 66%, #eddcb1 82%, #f1dfb4 100%);
  }
  .home__crest {
    position: absolute;
    top: 0;
    left: 0;
    width: 1200px;
    height: 190px;
  }
  .brand {
    position: absolute;
    top: 96px;
    left: 0;
    width: 1200px;
    display: flex;
    justify-content: center;
    align-items: center;
    gap: 12px;
  }
  .brand__dot {
    width: 16px;
    height: 16px;
    background: var(--brand-blue);
    border-radius: 50%;
  }
  .brand__name {
    font-family: "Oswald", sans-serif;
    font-weight: 500;
    font-size: 30px;
    line-height: 36px;
    letter-spacing: 1px;
    color: var(--brand-blue);
  }
  .hero {
    position: absolute;
    left: 183px;
    top: 330px;
    width: 834px;
    height: 251px;
    background: var(--panel);
    border: 1.5px solid var(--white);
    border-radius: 4px;
  }
  .hero__kicker {
    position: absolute;
    left: 321px;
    top: -15px;
    width: 192px;
    height: 28px;
    border-radius: 14px;
    background: var(--brand-blue);
    color: var(--white);
    font-weight: 500;
    font-size: 23px;
    line-height: 28px;
    letter-spacing: 3px;
    text-align: center;
  }
  .hero__headline {
    position: absolute;
    left: 0;
    top: 26px;
    width: 100%;
    text-align: center;
    color: var(--ink);
    font-weight: 600;
    font-size: 82px;
    line-height: 80px;
    letter-spacing: 10px;
    white-space: nowrap;
  }
  .hero__sub {
    position: absolute;
    left: 31px;
    top: 208px;
    width: 772px;
    height: 28px;
    border-radius: 14px;
    background: var(--mid-blue);
    color: var(--white);
    font-weight: 500;
    font-size: 23.5px;
    line-height: 28px;
    letter-spacing: 2.6px;
    text-align: center;
    white-space: nowrap;
  }
  .cta {
    position: absolute;
    left: 418px;
    top: 581px;
    width: 364px;
    height: 56px;
    background: var(--brand-green);
    border-radius: 0 0 18px 18px;
    color: var(--white);
    font-family: "Poppins", sans-serif;
    font-weight: 600;
    font-size: 17px;
    line-height: 56px;
    text-align: center;
    text-decoration: none;
    letter-spacing: -0.2px;
  }
</style>
</head>
<body>
  <main class="home">
    <div class="home__scene" role="img" aria-label="Sunny tropical beach with calm turquoise water, palm trees and pale sand under a bright blue sky"></div>

    <svg class="home__crest" viewBox="0 0 1200 190" aria-hidden="true">
      <path fill="#ffffff" d="M0,0 H1200 V34 C1100,18 1010,40 930,100 C860,150 760,166 660,170 C630,172 618,186 600,186 C582,186 570,172 540,170 C440,166 340,150 270,100 C190,40 100,18 0,34 Z"/>
    </svg>

    <header class="brand">
      <span class="brand__dot"></span>
      <span class="brand__name">Sunset Harbor Living</span>
    </header>

    <section class="hero">
      <div class="hero__kicker">IMAGINE A</div>
      <h1 class="hero__headline">RETIREMENT WHERE<br>YOUR DREAMS</h1>
      <p class="hero__sub">ARE BROUGHT TO LIFE,AND YOU HAVE NEVER FELT MORE ALIVE.</p>
    </section>

    <a class="cta" href="#contents">LET US SHOW YOU HOW</a>
  </main>
</body>
</html>
```